Vegan bakery needs business card

We need a business card design for my vegan bakery in Philadelphia Pa. We create amazing whole food plant based cuisine that is egg and dairy free. We use fruits, vegetables, healing herbs, nuts, natural sugars (date, turbinado, agave) and non bleached flours in our creations. Due to demand and interest in the Philadelphia area we created a late night vegan dessert delivery service named Bramble Vegan. We are the only business providing delicious vegan desserts delivered to your door at 1am!! We would like to see designs that use the color scheme in the logo. The final design should communicate the benefits of our products: dairy/egg free, plant based, healing herbs, amazing food.

```html
<!DOCTYPE html>
<html lang="en">
<head>
<meta charset="utf-8">
<title>Bramble Vegan – Business Card</title>
<link href="https://fonts.googleapis.com/css2?family=Questrial&display=swap" rel="stylesheet">
<style>
  :root {
    --backdrop: #2e2e2e;
    --card: #1d1d1d;
    --salmon: #f0826b;
    --green: #6cc43c;
    --ink: #efefef;
    --silver: #8c8c8c;
    --font: "Questrial", "Century Gothic", sans-serif;
  }
  * { margin: 0; padding: 0; box-sizing: border-box; }
  html, body {
    width: 1200px; height: 1189px; overflow: hidden;
    background: var(--backdrop);
    font-family: var(--font);
  }
  .canvas { position: relative; width: 1200px; height: 1189px; }
  .card {
    position: absolute; left: 150px; width: 900px; height: 514px;
    background: var(--card); border-radius: 34px; overflow: hidden;
  }
  .card--back { top: 60px; }
  .card--front { top: 615px; }

  /* back */
  .back-mark {
    position: absolute; left: 0; right: 0; top: 150px;
    display: flex; align-items: center; justify-content: center; gap: 22px;
    color: var(--silver); font-size: 64px; letter-spacing: 1px;
  }
  .back-mark .dot { width: 54px; height: 54px; border-radius: 50%; background: var(--silver); }
  .products-label {
    position: absolute; left: 0; right: 0; top: 300px; text-align: center;
    color: var(--green); font-size: 22px; letter-spacing: 0.5px;
  }
  .products-list {
    position: absolute; left: 0; right: 0; top: 334px; text-align: center;
    color: var(--salmon); font-size: 27px;
  }

  /* front */
  .brand {
    position: absolute; left: 60px; top: 150px; width: 380px; text-align: center;
  }
  .brand-name {
    display: flex; align-items: center; justify-content: center; gap: 14px;
    color: var(--salmon); font-size: 46px;
  }
  .brand-name .dot { width: 34px; height: 34px; border-radius: 50%; background: var(--salmon); }
  .tagline {
    margin-top: 34px; color: var(--green); font-size: 34px; line-height: 1.05; font-weight: 700;
  }
  .contact { position: absolute; left: 515px; top: 78px; width: 360px; }
  .person-name { color: var(--salmon); font-size: 32px; font-weight: 400; }
  .person-title { color: var(--ink); font-size: 19px; margin-top: 2px; }
  .rule-name { height: 2px; background: var(--green); width: 330px; margin: 14px 0 22px; }
  .contact-lines { list-style: none; }
  .contact-lines li {
    display: flex; align-items: center; gap: 12px;
    color: var(--ink); font-size: 22px; line-height: 31px;
  }
  .contact-lines svg { width: 22px; height: 22px; flex: none; }
  .company { color: var(--salmon); font-size: 22px; margin-top: 22px; }
  .address { color: var(--ink); font-size: 22px; line-height: 29px; }

  .footer {
    position: absolute; left: 80px; right: 0; top: 440px; height: 36px;
    display: flex; align-items: center; gap: 16px;
  }
  .footer-rule { height: 2px; background: var(--green); }
  .footer-rule--left { width: 450px; flex: none; }
  .footer-rule--right { flex: 1; min-width: 40px; }
  .website { color: var(--green); font-size: 24px; white-space: nowrap; flex: none; }
</style>
</head>
<body>
<main class="canvas">

  <section class="card card--back">
    <div class="back-mark"><span class="dot"></span><span>Bramble Vegan</span></div>
    <p class="products-label">OUR PRODUCTS</p>
    <p class="products-list">dairy/egg free, plant based, healing herbs, amazing food.</p>
  </section>

  <section class="card card--front">
    <div class="brand">
      <div class="brand-name"><span class="dot"></span><span>Bramble Vegan</span></div>
      <p class="tagline">100% vegan<br>100% delicious</p>
    </div>

    <div class="contact">
      <h1 class="person-name">Jordan Reyes</h1>
      <p class="person-title">Director of Marketing</p>
      <div class="rule-name"></div>
      <ul class="contact-lines">
        <li>
          <svg viewBox="0 0 24 24" fill="none" stroke="var(--salmon)" stroke-width="2"><circle cx="12" cy="12" r="10.5"/><rect x="8.5" y="6" width="7" height="12" rx="1.2"/></svg>
          215-555-0147
        </li>
        <li>
          <svg viewBox="0 0 24 24" fill="none" stroke="var(--salmon)" stroke-width="2"><circle cx="12" cy="12" r="10.5"/><path d="M7 10c0-2 10-2 10 0M8.5 11l-1 5h9l-1-5z"/></svg>
          215-555-0192
        </li>
        <li>
          <svg viewBox="0 0 24 24" fill="none" stroke="var(--salmon)" stroke-width="2"><circle cx="12" cy="12" r="10.5"/><rect x="6.5" y="8" width="11" height="8"/><path d="M6.5 8l5.5 4.5L17.5 8"/></svg>
          hello@bramblevegan.com
        </li>
      </ul>
      <p class="company">Bramble Vegan</p>
      <p class="address">Po Box 48, Larkspur Street<br>Philadelphia, PA 19107</p>
    </div>

    <div class="footer">
      <div class="footer-rule footer-rule--left"></div>
      <p class="website">www.bramblevegan.com</p>
      <div class="footer-rule footer-rule--right"></div>
    </div>
  </section>

</main>
</body>
</html>
```